Landing page design for my current website

I need a landing page designed for my Wordpress website. My website is Velmorquay.com, and I need a page that will serve as a landing page for online ads I run. Please follow the color scheme of the current website

This web page will be targeted towards real estate owners who are looking for a property manager. Above the fold needs to have a CTA form headlined with "As a Rental Property Owner, I Want More Protection, Less Stress, and Drama-Free Living"

A few highlights that can be listed beyond the CTA and fold

- Comprehensive Property Management
Full-service management covering tenant placement, leasing, maintenance, and inspections.

Maximized Rental Income
Proven strategies to optimize rental rates and minimize vacancies, ensuring higher ROI.

Stress-Free Management
We handle all tenant interactions, maintenance requests, and property issues, so you don't have to.

Experienced Team
Over a decade of experience in managing single-family homes, small multifamily units, and apartment complexes.

Advanced Technology
Utilize cutting-edge property management software for efficient communication, rent collection, and maintenance tracking.

Tenant Screening and Placement
Thorough background checks and tenant screening processes to ensure reliable and responsible tenants.

Regular Property Inspections
Routine inspections to maintain property condition and address issues before they become costly problems.

Legal Compliance
Expertise in local and federal rental laws to keep your properties compliant and avoid legal hassles.

Transparent Reporting
Detailed monthly reports and financial statements to keep you informed about your property's performance.

Personalized Service
Tailored management plans to meet the unique needs of your properties and investment goals.
Effective Tenant Conflict Resolution
Skilled in handling challenging tenant situations, ensuring conflicts are resolved quickly and professionally to maintain a peaceful living environment and protect your investment.

```html
<!DOCTYPE html>
<html lang="en">
<head>
<meta charset="utf-8">
<title>Velmorquay Realty – Property Management</title>
<link href="https://fonts.googleapis.com/css2?family=Roboto:wght@400;500;700&family=Lato:wght@400;700&display=swap" rel="stylesheet">
<style>
:root{
  --navy:#11457a;
  --navy-deep:#0d3a68;
  --blue:#1a6db3;
  --ink:#2b2b2b;
  --muted:#444;
  --white:#fff;
  --line:#d5d9de;
}
*{box-sizing:border-box;margin:0;padding:0}
html,body{width:701px;height:1200px;overflow:hidden;background:var(--white)}
body{font-family:"Lato",sans-serif;color:var(--ink);position:relative}
.site-header{height:60px;display:flex;align-items:center;padding:0 66px;position:relative}
.brand{display:flex;align-items:center;gap:10px}
.brand-dot{width:36px;height:36px;border-radius:50%;background:var(--navy)}
.brand-name{font-family:"Roboto",sans-serif;font-weight:700;color:var(--navy);font-size:20px;line-height:1;letter-spacing:.5px}
.call{position:absolute;left:460px;top:13px;display:flex;align-items:center;gap:12px}
.call-icon{width:34px;height:34px;border-radius:50%;background:var(--navy);display:flex;align-items:center;justify-content:center}
.call-label{font-family:"Roboto",sans-serif;font-size:9px;color:var(--ink)}
.call-number{font-family:"Roboto",sans-serif;font-size:12px;color:var(--navy)}
.menu{position:absolute;left:612px;top:22px;width:22px}
.menu span{display:block;height:2px;background:var(--ink);margin-bottom:5.5px}

.hero{position:absolute;top:60px;left:0;width:701px;height:350px}
.hero-copy{position:absolute;left:0;top:0;width:350px;height:350px;background:var(--navy);padding:67px 0 0 65px;color:var(--white)}
.welcome{display:inline-block;background:var(--navy-deep);font-family:"Roboto",sans-serif;font-size:14px;padding:4px 27px 5px}
.hero-title{font-family:"Roboto",sans-serif;font-weight:700;font-size:25px;line-height:32px;margin-top:18px}
.hero-text{font-size:8.6px;line-height:15px;margin-top:11px;width:248px}
.btn-light{display:inline-block;margin-top:18px;background:var(--white);color:var(--navy);font-family:"Roboto",sans-serif;font-weight:500;font-size:9px;width:98px;height:25px;line-height:25px;text-align:center}
.hero-photo{position:absolute;left:350px;top:0;width:351px;height:350px;background:linear-gradient(160deg,#6d6259 0%,#8a5a48 35%,#5c4a42 65%,#4b5a3e 100%)}
.lead-form{position:absolute;left:412px;top:35px;width:227px;height:281px;background:var(--white);border-radius:3px;padding:20px 20px 0}
.lead-form h2{font-family:"Roboto",sans-serif;font-weight:500;color:var(--navy);font-size:14.5px;line-height:20px;text-align:center}
.field{border:1px solid var(--line);height:28px;margin-top:8px;font-family:"Roboto",sans-serif;font-size:7px;color:#555;padding:10px 8px}
.field:first-of-type{margin-top:14px}
.field.area{height:63px;padding-top:10px}
.submit{margin-top:9px;background:var(--navy);color:var(--white);height:25px;line-height:25px;text-align:center;font-family:"Roboto",sans-serif;font-size:9px}

.features{position:absolute;top:410px;left:0;width:701px;height:430px;background:linear-gradient(180deg,#fbfcfd 0%,#eef1f4 60%,#e3e7ec 100%)}
.feature{position:absolute;width:135px}
.feature h3{font-family:"Lato",sans-serif;font-weight:700;color:var(--navy);font-size:10px;line-height:12.5px}
.feature p{font-size:7.5px;line-height:10px;color:var(--muted);margin-top:3px}
.feature.center{text-align:center;width:175px}
.hub-name{position:absolute;left:265px;top:140px;width:160px;text-align:center;font-family:"Roboto",sans-serif;font-weight:500;color:var(--navy);font-size:22px;line-height:27px}
.house-photo{position:absolute;top:840px;left:0;width:701px;height:330px;background:linear-gradient(180deg,#e2e5e9 0%,#b9aa98 35%,#8b7f70 70%,#6b7a55 100%)}
.site-footer{position:absolute;top:1170px;left:0;width:701px;height:30px;background:var(--navy);color:var(--white);font-size:7.5px;text-align:center;line-height:30px}
</style>
</head>
<body>
<header class="site-header">
  <div class="brand">
    <div class="brand-dot"></div>
    <div class="brand-name">VELMORQUAY REALTY</div>
  </div>
  <div class="call">
    <div class="call-icon"><svg width="14" height="14" viewBox="0 0 24 24"><path fill="#fff" d="M6.6 10.8a15 15 0 006.6 6.6l2.2-2.2c.3-.3.7-.4 1-.2 1.1.4 2.3.6 3.6.6.6 0 1 .4 1 1V20c0 .6-.4 1-1 1A17 17 0 013 4c0-.6.4-1 1-1h3.5c.6 0 1 .4 1 1 0 1.3.2 2.5.6 3.6.1.3 0 .7-.2 1z"/></svg></div>
    <div><div class="call-label">Call or Text</div><div class="call-number">555.014.2290</div></div>
  </div>
  <div class="menu"><span></span><span></span><span></span></div>
</header>

<section class="hero">
  <div class="hero-copy">
    <div class="welcome">Welcome to</div>
    <h1 class="hero-title">Homes &amp; Apartments<br>for Rent</h1>
    <p class="hero-text">Velmorquay, Inc. offers affordable, safe, up-to-date housing options in the Bloomsburg, Danville, and Berwick Pennsylvania markets. Contact us today if you’re looking for your next rental.</p>
    <a class="btn-light">Contact Us</a>
  </div>
  <div class="hero-photo" role="img" aria-label="Couple standing in front of a brick rental house"></div>
  <form class="lead-form">
    <h2>As a Rental Property Owner, I Want More Protection, Less Stress, and Drama-Free Livin</h2>
    <div class="field">Name</div>
    <div class="field">Email Address</div>
    <div class="field area">Message</div>
    <div class="submit">Submit</div>
  </form>
</section>

<section class="features">
  <svg width="701" height="430" style="position:absolute;left:0;top:0">
    <circle cx="345" cy="163" r="80" fill="#fff" style="filter:drop-shadow(0 2px 6px rgba(0,0,0,.12))"/>
    <path d="M267 102 A106 106 0 1 0 424 102" fill="none" stroke="#11457a" stroke-width="2.5"/>
    <g fill="#fff" stroke="#11457a" stroke-width="3">
      <circle cx="267" cy="102" r="4.5"/><circle cx="247" cy="141" r="4.5"/><circle cx="247" cy="187" r="4.5"/>
      <circle cx="267" cy="226" r="4.5"/><circle cx="305" cy="256" r="4.5"/><circle cx="345" cy="264" r="4.5"/>
      <circle cx="386" cy="256" r="4.5"/><circle cx="424" cy="226" r="4.5"/><circle cx="443" cy="187" r="4.5"/>
      <circle cx="444" cy="141" r="4.5"/><circle cx="424" cy="102" r="4.5"/>
    </g>
    <g fill="#fff" stroke="#1a6db3" stroke-width="2">
      <circle cx="233" cy="75" r="24"/><circle cx="208" cy="138" r="24"/><circle cx="209" cy="204" r="24"/>
      <circle cx="233" cy="260" r="24"/><circle cx="276" cy="305" r="24"/><circle cx="345" cy="313" r="24"/>
      <circle cx="414" cy="305" r="24"/><circle cx="457" cy="260" r="24"/><circle cx="482" cy="204" r="24"/>
      <circle cx="483" cy="138" r="24"/><circle cx="457" cy="75" r="24"/>
    </g>
    <g fill="none" stroke="#1a6db3" stroke-width="1.3" stroke-linejoin="round">
      <path d="M224 78 l9-8 9 8 M226 77 v8 h14 v-8"/>
      <path d="M199 138 l9-9 9 9 M201 137 v10 h14 v-10 M202 143 h12"/>
      <circle cx="205" cy="200" r="4"/><path d="M199 212 q6 -4 12 0 l8 -3"/>
      <circle cx="228" cy="256" r="3.5"/><circle cx="238" cy="256" r="3.5"/><path d="M222 267 q6-7 12 0 q6-7 12 0"/>
      <rect x="268" y="297" width="16" height="16" rx="1"/><path d="M272 305 h8 M276 301 v8"/>
      <circle cx="345" cy="306" r="4"/><path d="M336 322 v-6 h18 v6 M340 316 v6 M350 316 v6"/>
      <circle cx="414" cy="299" r="5"/><path d="M405 316 q9-10 18 0 z"/>
      <rect x="448" y="250" width="16" height="20"/><path d="M452 265 v-4 M456 265 v-7 M460 265 v-5"/>
      <rect x="474" y="196" width="13" height="16"/><path d="M477 201 h7 M477 205 h7 M486 196 l5 2 v5 q0 4-5 6"/>
      <path d="M474 138 l8-8 8 8 M476 137 v10 h10"/><circle cx="488" cy="145" r="3.5"/><path d="M490 148 l3 3"/>
      <path d="M449 82 q8-5 16 -3 l6-4 M457 68 a3 3 0 1 1 0.1 0 M457 71 v6"/>
    </g>
  </svg>
  <div class="hub-name">Velmorquay Realty</div>

  <div class="feature" style="left:61px;top:52px;width:125px"><h3>Comprehensive Property Management</h3><p>Full-service management covering tenant placement, leasing, maintenance, and inspections.</p></div>
  <div class="feature" style="left:54px;top:124px;width:115px"><h3>Maximized Rental Income</h3><p>Proven strategies to optimize rental rates and minimize vacancies, ensuring higher ROI.</p></div>
  <div class="feature" style="left:56px;top:188px;width:130px"><h3>Stress-Free<br>Management</h3><p>We handle all tenant interactions, maintenance requests, and property issues, so you don't have to.</p></div>
  <div class="feature" style="left:61px;top:260px;width:150px"><h3>Experienced Team</h3><p>Over a decade of experience in managing single-family homes, small multifamily units, and apartment complexes.</p></div>
  <div class="feature" style="left:86px;top:321px;width:155px"><h3>Advanced Technology</h3><p>Utilize cutting-edge property management software for efficient communication, rent collection, and maintenance tracking.</p></div>
  <div class="feature center" style="left:258px;top:353px"><h3>Effective Tenant Conflict<br>Resolution</h3><p>Skilled in handling challenging tenant situations, ensuring conflicts are resolved quickly and professionally to maintain a peaceful living environment and protect your investment.</p></div>
  <div class="feature" style="left:512px;top:52px;width:135px"><h3>Tenant Screening and Placement</h3><p>Thorough background checks and tenant screening processes to ensure reliable and responsible tenants.</p></div>
  <div class="feature" style="left:521px;top:124px;width:110px"><h3 style="white-space:nowrap">Regular Property Inspections</h3><p>Routine inspections to maintain property condition and address issues before they become costly problems.</p></div>
  <div class="feature" style="left:522px;top:193px;width:130px"><h3>Legal Compliance</h3><p>Expertise in local and federal rental laws to keep your properties compliant and avoid legal hassles.</p></div>
  <div class="feature" style="left:508px;top:256px;width:140px"><h3>Transparent Reporting</h3><p>Detailed monthly reports and financial statements to keep you informed about your property's performance.</p></div>
  <div class="feature" style="left:479px;top:318px;width:145px"><h3>Personalized Service</h3><p>Tailored management plans to meet the unique needs of your properties and investment goals.</p></div>
</section>

<div class="house-photo" role="img" aria-label="Two-storey suburban house with gabled roof, double garage and flowering tree"></div>

<footer class="site-footer">Copyright © 2024 Velmorquay Realty. All rights reserved.</footer>
</body>
</html>
```